Website Design for a holiday home letting busines

We require a redesign of our present website www.pinebrookstays.com. We want the website to stand out and look professional and clean to make holiday hunters want to book a caravan or lodge holiday with us. Our logo is red however we DO NOT want the website to be red. We want a natural colour scheme.

The final design should communicate that we are a professional company to book with.

On the home page we require;
Overview of company
Photo
Search box for holiday (check in)
Late Deals
Reviews
News

We would like the following pages designed; home page, available dates page, caravans page, content page.

The website should be responsive for smart phones. One website I do like is http://www.verdoliso.be/nl/

Target Market(s)

Families

Industry/Entity Type

Travel

Number of Pages Required

5+ page

Font styles to use
Serif

Requirements
Must have
• The project must be responsive for mobile phones and tablets.
• Ability to search for holiday home holidays
• We want a natural colour scheme.
Nice to have
• A style we like is http://www.verdoliso.be/nl/
Should not have
• Do not use red as a colour for the website. Our logo is red so this is the only time we want this used.

```html
<!DOCTYPE html>
<html lang="en">
<head>
<meta charset="utf-8">
<title>Pinebrook Stays – Caravan and Lodge Holidays</title>
<link href="https://fonts.googleapis.com/css2?family=Lora:wght@400;500;600;700&display=swap" rel="stylesheet">
<style>
:root{
  --logo:#c7262b;
  --accent:#5d7a46;
  --accent-dark:#465e34;
  --earth:#8b6a44;
  --ink:#2e2b26;
  --muted:#857f75;
  --line:#e2ded6;
  --band:#f1eee8;
  --white:#ffffff;
  --footer:#2a2a24;
  --footer-deep:#1f1f1a;
  --footer-text:#b3aea2;
}
*{box-sizing:border-box;margin:0;padding:0}
html,body{width:1200px;height:3100px;overflow:hidden}
body{font-family:'Lora',serif;color:var(--ink);background:var(--white);font-size:13px;line-height:1.5}
.wrap{width:1040px;margin:0 auto;position:relative}

/* top bar */
.topbar{height:100px;display:flex;align-items:center}
.topbar .wrap{display:flex;align-items:center;justify-content:space-between}
.brand{display:flex;align-items:center;gap:12px;font-weight:700;font-size:26px;color:var(--logo)}
.brand-mark{width:34px;height:34px;border-radius:50%;background:var(--logo)}
.contact-strip{display:flex;align-items:center;gap:18px;font-size:12px;color:var(--muted)}
.contact-strip span{display:flex;align-items:center;gap:6px}
.live-chat{border:1px solid var(--line);padding:7px 16px;font-size:12px;color:var(--ink)}
.chat-dot{width:36px;height:36px;border-radius:50%;background:var(--accent);display:flex;align-items:center;justify-content:center}

/* nav */
.mainnav{height:40px;border-top:1px solid var(--line);border-bottom:1px solid var(--line)}
.mainnav ul{list-style:none;display:flex;justify-content:space-between;height:38px;align-items:center}
.mainnav li{font-size:12px;color:#555}
.mainnav li.active{color:var(--accent);font-weight:700}

/* hero */
.hero{height:508px;position:relative;background:linear-gradient(135deg,#7f8b8f 0%,#b9b3a3 35%,#8c9a6d 65%,#5c6a44 100%)}
.search-panel{position:absolute;left:80px;bottom:60px;width:720px;height:96px;background:var(--white);display:flex;align-items:center;padding:0 22px;gap:20px;box-shadow:0 2px 10px rgba(0,0,0,.15)}
.search-label{font-size:12px;font-weight:700;letter-spacing:3px;color:var(--accent);line-height:1.1}
.search-label b{display:block;font-size:27px;letter-spacing:1px;color:var(--ink);font-weight:700}
.field{display:flex;flex-direction:column;gap:4px;font-size:11px;color:#555}
.field .input{height:30px;border:1px solid var(--line);background:#faf9f6}
.find-btn{background:var(--accent);color:var(--white);font-weight:700;font-size:17px;width:110px;height:44px;display:flex;align-items:center;justify-content:center;margin-left:auto}

/* overview */
.overview{height:372px;padding-top:64px}
.overview .wrap{display:flex;gap:36px}
.video-thumb{width:320px;height:210px;flex:none;background:linear-gradient(180deg,#6fb4d8 0%,#b9dff0 55%,#c89a6a 100%)}
.section-title{font-size:27px;font-weight:400;color:var(--ink);margin-bottom:14px}
.overview p{color:#6f6a62;font-size:12.5px;line-height:1.8;margin-bottom:20px}
.btn{display:inline-block;background:var(--accent);color:var(--white);font-size:12px;font-weight:700;padding:8px 18px}

/* listings */
.listing{background:var(--band);height:560px;padding-top:48px}
.listing.plain{background:var(--white);height:540px}
.listing-head{display:flex;justify-content:space-between;align-items:center;margin-bottom:26px}
.listing-head .section-title{margin:0}
.arrows{display:flex;gap:4px}
.arrow{width:22px;height:22px;border-radius:50%;background:#bdb7ab;display:flex;align-items:center;justify-content:center}
.arrow.on{background:var(--accent)}
.cards{display:flex;gap:31px}
.card{width:326px;background:var(--white);border:1px solid var(--line)}
.card-photo{height:210px;position:relative}
.price{position:absolute;top:12px;left:0;background:var(--accent);color:var(--white);font-size:13px;font-weight:700;padding:4px 10px}
.price small{font-weight:400;font-size:10px}
.card-body{padding:16px 16px 14px}
.card-body h3{font-size:15px;font-weight:700;line-height:1.35;margin-bottom:8px}
.card-body p{font-size:11.5px;color:var(--muted);line-height:1.65}
.card-meta{display:flex;justify-content:space-between;border-top:1px solid var(--line);padding:10px 16px;font-size:11px;color:var(--muted)}
.card-meta span{display:flex;align-items:center;gap:5px}
.card-meta span::before{content:"";width:7px;height:7px;background:var(--earth)}
.dots{display:flex;justify-content:center;gap:6px;margin-top:22px}
.dots i{width:7px;height:7px;border-radius:50%;background:#bdb7ab}
.dots i.on{background:#555}
.p1{background:linear-gradient(160deg,#8a5a3a,#d7b48a 60%,#f0e2cc)}
.p2{background:linear-gradient(180deg,#8cc2ea 0%,#d9ecf7 45%,#e9e9e9 60%,#7fa65a 100%)}
.p3{background:linear-gradient(160deg,#5d3b26,#c7985e 55%,#f4e6d2)}
.p4{background:linear-gradient(160deg,#dfe8ee,#a8c3cf 50%,#f0ede6)}
.p5{background:linear-gradient(180deg,#4a5360 0%,#8a8f95 40%,#3d87a8 75%,#2c2c2c 100%)}
.p6{background:linear-gradient(160deg,#f2ece2,#d8cbb3 55%,#9b8a6c)}

/* community, blog, reviews */
.trio{background:var(--band);height:580px;padding-top:44px}
.trio .wrap{display:flex;gap:32px}
.col{width:325px}
.col-head{display:flex;justify-content:space-between;align-items:center;margin-bottom:18px}
.col-head h2{font-size:24px;font-weight:400}
.chev{color:var(--accent);font-size:20px;font-weight:700;letter-spacing:6px}
.feed-box{background:var(--white);border:1px solid var(--line);height:430px;padding:14px}
.feed-top{display:flex;gap:10px;margin-bottom:12px}
.feed-cover{width:64px;height:64px;background:linear-gradient(135deg,#9bb7c9,#d6c7a8)}
.feed-top b{font-size:13px;color:var(--accent-dark)}
.feed-top p{font-size:11px;color:var(--muted)}
.feed-post{border-top:1px solid var(--line);padding:10px 0;font-size:11px;color:#666}
.feed-post b{color:var(--accent-dark);display:block}
.feed-faces{display:flex;gap:6px;margin-top:8px}
.feed-faces i{width:40px;height:40px;background:#d3cfc5}
.list-item{display:flex;gap:12px;margin-bottom:22px}
.thumb{width:80px;height:80px;flex:none}
.list-item h4{font-size:13px;font-weight:700;line-height:1.3;margin-bottom:4px}
.list-item p{font-size:11px;color:var(--muted);line-height:1.5}
.list-item .more{font-size:11px;color:var(--ink);font-weight:700;text-align:right;margin-top:3px}
.review{display:flex;gap:14px;margin-bottom:24px;align-items:flex-start}
.avatar{width:62px;height:62px;border-radius:50%;flex:none;background:linear-gradient(135deg,#c8b09a,#8f7664)}
.review p{font-size:11px;color:var(--muted);line-height:1.55}
.review b{display:block;text-align:right;font-size:11px;margin-top:3px}

/* footer */
.site-footer{background:var(--footer);color:var(--footer-text);padding:48px 0 0;height:340px}
.site-footer .wrap{display:flex;gap:40px}
.fcol{width:230px}
.fcol h5{color:var(--white);font-size:13px;font-weight:700;letter-spacing:1px;margin-bottom:16px}
.map{height:160px;background:linear-gradient(135deg,#d9d6cf,#c5d3c0 50%,#bcd0de)}
.event{font-size:11px;margin-bottom:18px;line-height:1.6}
.event b{color:var(--white);display:block}
.event .more{color:var(--white);text-align:right}
.addr{font-size:11px;line-height:1.9}
.addr div{display:flex;gap:8px;align-items:flex-start}
.addr svg{margin-top:4px;flex:none}
.fcol .finput{height:26px;background:#36362f;border:1px solid #45453c;margin-bottom:8px;font-size:10px;padding:5px 8px;color:#8d897f}
.fcol .fsubmit{background:var(--accent);color:var(--white);font-size:10px;font-weight:700;padding:5px 12px;float:right}
.bottom-bar{background:var(--footer-deep);height:60px;color:#8d897f;font-size:11px}
.bottom-bar .wrap{display:flex;justify-content:space-between;align-items:center;height:60px}
.socials{display:flex;gap:8px}
.socials i{width:18px;height:18px;border-radius:50%;background:#6d6a62}
</style>
</head>
<body>

<header class="topbar">
  <div class="wrap">
    <div class="brand"><span class="brand-mark"></span>Pinebrook Stays</div>
    <div class="contact-strip">
      <span><svg width="12" height="12" viewBox="0 0 12 12"><path d="M2 1h3l1 3-2 1a7 7 0 0 0 3 3l1-2 3 1v3c-6 1-10-3-9-9z" fill="#5d7a46"/></svg>01632 960 418</span>
      <span><svg width="14" height="10" viewBox="0 0 14 10"><rect x="0.5" y="0.5" width="13" height="9" fill="none" stroke="#5d7a46"/><path d="M1 1l6 5 6-5" fill="none" stroke="#5d7a46"/></svg>info@pinebrookstays.com</span>
      <span class="live-chat">Live Chat</span>
      <span class="chat-dot"><svg width="16" height="14" viewBox="0 0 16 14"><path d="M1 1h14v9H6l-3 3v-3H1z" fill="#fff"/></svg></span>
    </div>
  </div>
</header>

<nav class="mainnav">
  <ul class="wrap">
    <li class="active">Home</li><li>News</li><li>Reviews</li><li>Caravans &amp; Lodges</li><li>Park Facilities</li><li>Local Attractions</li><li>Available Dates</li><li>Late Deals</li><li>Special Offers</li><li>Contact Us</li>
  </ul>
</nav>

<section class="hero" role="img" aria-label="Touring motorhome driving on a sunny mountain road">
  <div class="search-panel">
    <div class="search-label">SEARCH<b>HERE</b></div>
    <div class="field" style="width:170px">Name<div class="input"></div></div>
    <div class="field" style="width:150px">Check in date<div class="input"></div></div>
    <div class="field" style="width:120px">How many nights<div class="input"></div></div>
    <div class="find-btn">FIND</div>
  </div>
</section>

<section class="overview">
  <div class="wrap">
    <div class="video-thumb" role="img" aria-label="Video still: family relaxing in a holiday lodge living room"></div>
    <div>
      <h2 class="section-title">Company Overview</h2>
      <p>Welcome to Pinebrook Stays, your home for relaxing caravan and lodge holidays across the country. We are a family run business with many years of experience helping guests find the right place to unwind. Every one of our holiday homes is cleaned, checked and prepared before you arrive, so you can simply unpack and enjoy your break. Our parks offer fresh air, open green space, play areas for children and easy access to beaches, forests and local towns. Browse our caravans and lodges, check available dates and book your next family holiday with confidence today.</p>
      <span class="btn">Read More</span>
    </div>
  </div>
</section>

<section class="listing">
  <div class="wrap">
    <div class="listing-head">
      <h2 class="section-title">Our caravans and lodges</h2>
      <div class="arrows">
        <span class="arrow on"><svg width="6" height="8" viewBox="0 0 6 8"><path d="M5 0L1 4l4 4" fill="none" stroke="#fff" stroke-width="1.5"/></svg></span>
        <span class="arrow"><svg width="6" height="8" viewBox="0 0 6 8"><path d="M1 0l4 4-4 4" fill="none" stroke="#fff" stroke-width="1.5"/></svg></span>
      </div>
    </div>
    <div class="cards">
      <article class="card">
        <div class="card-photo p1" role="img" aria-label="Lodge bedroom with a made double bed"><span class="price">£12.99 <small>/Night</small></span></div>
        <div class="card-body"><h3>Lorem ipsum dolor sit amet, consect</h3><p>Bright two bedroom lodge with a large decking area, fitted kitchen and quiet woodland views across the park.</p></div>
        <div class="card-meta"><span>3 Bedrooms</span><span>Sleeps 6</span><span>Lodge</span></div>
      </article>
      <article class="card">
        <div class="card-photo p2" role="img" aria-label="Static caravan on a grassy pitch under blue sky"><span class="price">£11.99 <small>/Night</small></span></div>
        <div class="card-body"><h3>Lorem ipsum dolor sit amet, consect</h3><p>Spacious modern caravan close to the play park, with a cosy lounge, double glazing and central heating.</p></div>
        <div class="card-meta"><span>2 Bedrooms</span><span>Sleeps 4</span><span>Caravan</span></div>
      </article>
      <article class="card">
        <div class="card-photo p3" role="img" aria-label="Warm lit lodge bedroom interior"><span class="price">£12.99 <small>/Night</small></span></div>
        <div class="card-body"><h3>Lorem ipsum dolor sit amet, consect</h3><p>Luxury lodge with hot tub, open plan living space and a private garden ideal for families and friends.</p></div>
        <div class="card-meta"><span>3 Bedrooms</span><span>Sleeps 6</span><span>Lodge</span></div>
      </article>
    </div>
    <div class="dots"><i class="on"></i><i></i><i></i></div>
  </div>
</section>

<section class="listing plain">
  <div class="wrap">
    <div class="listing-head">
      <h2 class="section-title">Late Deals</h2>
      <div class="arrows">
        <span class="arrow"><svg width="6" height="8" viewBox="0 0 6 8"><path d="M1 0l4 4-4 4" fill="none" stroke="#fff" stroke-width="1.5"/></svg></span>
      </div>
    </div>
    <div class="cards">
      <article class="card">
        <div class="card-photo p4" role="img" aria-label="Guests toasting with drinks on holiday"><span class="price">£11.99 <small>/Night</small></span></div>
        <div class="card-body"><h3>Lorem ipsum dolor sit amet, consect</h3><p>Short break offer for the coming weekend, three nights in a family caravan at a reduced price.</p></div>
        <div class="card-meta"><span>2 Bedrooms</span><span>Sleeps 4</span><span>Caravan</span></div>
      </article>
      <article class="card">
        <div class="card-photo p5" role="img" aria-label="Lodge terrace with pool at dusk"><span class="price">£11.99 <small>/Night</small></span></div>
        <div class="card-body"><h3>Lorem ipsum dolor sit amet, consect</h3><p>Midweek lodge deal with pool access and outdoor terrace, available for selected dates this month.</p></div>
        <div class="card-meta"><span>3 Bedrooms</span><span>Sleeps 6</span><span>Lodge</span></div>
      </article>
      <article class="card">
        <div class="card-photo p6" role="img" aria-label="Light lodge bedroom with neutral linen"><span class="price">£11.99 <small>/Night</small></span></div>
        <div class="card-body"><h3>Lorem ipsum dolor sit amet, consect</h3><p>Last minute saving on a quiet lodge by the lake, perfect for a relaxing family week away.</p></div>
        <div class="card-meta"><span>2 Bedrooms</span><span>Sleeps 4</span><span>Lodge</span></div>
      </article>
    </div>
  </div>
</section>

<section class="trio">
  <div class="wrap">
    <div class="col">
      <div class="col-head"><h2>Community</h2></div>
      <div class="feed-box">
        <div class="feed-top">
          <div class="feed-cover" role="img" aria-label="Page cover image of the holiday park"></div>
          <div><b>Pinebrook Community Page</b><p>1,280 people follow this page</p></div>
        </div>
        <div class="feed-post"><b>Pinebrook Stays</b>New spring dates are now open for booking on all lodges.</div>
        <div class="feed-post"><b>Pinebrook Stays</b>Thank you to every family who stayed with us this summer.</div>
        <div class="feed-post"><b>Pinebrook Stays</b>Our new play area opens next week, come and see it.</div>
        <div class="feed-faces"><i></i><i></i><i></i><i></i><i></i></div>
      </div>
    </div>
    <div class="col">
      <div class="col-head"><h2>Blog</h2><span class="chev">‹›</span></div>
      <div class="list-item"><div class="thumb p1" role="img" aria-label="Lodge interior"></div><div><h4>Lorem ipsum dolor sit amet, consectet</h4><p>Ideas for rainy day fun with the children near the park.</p><div class="more">Read More ›</div></div></div>
      <div class="list-item"><div class="thumb p2" role="img" aria-label="Caravan on grass"></div><div><h4>Lorem ipsum dolor sit amet, consectet</h4><p>Our guide to the best local walks and coastal trails.</p><div class="more">Read More ›</div></div></div>
      <div class="list-item"><div class="thumb p5" role="img" aria-label="Pool terrace"></div><div><h4>Lorem ipsum dolor sit amet, consectet</h4><p>What to pack for a relaxed family caravan holiday.</p><div class="more">Read More ›</div></div></div>
      <div class="list-item"><div class="thumb p3" role="img" aria-label="Cosy bedroom"></div><div><h4>Lorem ipsum dolor sit amet, consectet</h4><p>Seasonal events and markets happening this autumn.</p><div class="more">Read More ›</div></div></div>
    </div>
    <div class="col">
      <div class="col-head"><h2>Latest Reviews</h2><span class="chev">‹›</span></div>
      <div class="review"><div class="avatar" role="img" aria-label="Guest portrait"></div><div><p>Lovely clean lodge and friendly staff, the children did not want to leave at the end.</p><b>Guest Name</b></div></div>
      <div class="review"><div class="avatar" role="img" aria-label="Guest portrait"></div><div><p>Great location, easy booking and everything we needed for a restful week away.</p><b>Guest Name</b></div></div>
      <div class="review"><div class="avatar" role="img" aria-label="Guest portrait"></div><div><p>Our third stay here and it gets better every year. Already planning the next one.</p><b>Guest Name</b></div></div>
      <div class="review"><div class="avatar" role="img" aria-label="Guest portrait"></div><div><p>Spotless caravan, quiet park and beautiful views. Highly recommended for families.</p><b>Guest Name</b></div></div>
    </div>
  </div>
</section>

<footer>
  <div class="site-footer">
    <div class="wrap">
      <div class="fcol"><h5>LOCATION</h5><div class="map" role="img" aria-label="Map showing the park location"></div></div>
      <div class="fcol"><h5>EVENTS</h5>
        <div class="event"><b>Summer family fun day</b>Games, music and food for all ages on the main green.<div class="more">Read More ›</div></div>
        <div class="event"><b>Autumn lakeside walk</b>A guided walk around the lake with tea afterwards.<div class="more">Read More ›</div></div>
      </div>
      <div class="fcol"><h5>GET IN TOUCH</h5>
        <div class="addr">
          <div><svg width="10" height="13" viewBox="0 0 10 13"><path d="M5 0a5 5 0 0 0-5 5c0 4 5 8 5 8s5-4 5-8a5 5 0 0 0-5-5z" fill="#7f9a67"/></svg><span>Pinebrook Stays Ltd<br>12 Meadow Lane<br>Ashford Vale<br>AB1 2CD</span></div>
          <div><svg width="10" height="10" viewBox="0 0 12 12"><path d="M2 1h3l1 3-2 1a7 7 0 0 0 3 3l1-2 3 1v3c-6 1-10-3-9-9z" fill="#7f9a67"/></svg><span>01632 960 418</span></div>
          <div><svg width="12" height="9" viewBox="0 0 14 10"><rect x="0.5" y="0.5" width="13" height="9" fill="none" stroke="#7f9a67"/><path d="M1 1l6 5 6-5" fill="none" stroke="#7f9a67"/></svg><span>info@pinebrookstays.com</span></div>
        </div>
      </div>
      <div class="fcol"><h5>CONTACT</h5>
        <p style="font-size:11px;margin-bottom:12px">Send us your question and our team will reply soon.</p>
        <div class="finput">Name</div>
        <div class="finput">Email</div>
        <span class="fsubmit">SUBMIT</span>
      </div>
    </div>
  </div>
  <div class="bottom-bar">
    <div class="wrap"><span>© 2024 Pinebrook Stays. All rights reserved.</span><div class="socials"><i></i><i></i><i></i><i></i></div></div>
  </div>
</footer>

</body>
</html>
```